Business card por a urban DJ, up scale audience target

Need a sober design, modern, conservative colors but i can consider some options, y play rnb, hip hop, EDM and top40.

Business card for contact and personal info, double sided, use logo attrached please; im 42 so i need a card acording to my age an target audience.

Target Market(s)

Adult people, up scale audience

Industry/Entity Type

Music Download

Contact Information for Business Card

Cel (318) 4207265518 www.lumadrift.com

Requirements
Must have
• open mind
Nice to have
• open mind
Should not have
• DJ

```html
<!DOCTYPE html>
<html lang="en">
<head>
<meta charset="utf-8">
<title>Lumadrift Business Card</title>
<link rel="stylesheet" href="https://fonts.googleapis.com/css2?family=Noto+Sans:wght@400;700&display=swap">
<style>
  :root {
    --backdrop: #ebe4d8;
    --card: #ffffff;
    --ink: #2b2b2b;
    --rule: #3a3a3a;
  }
  * { margin: 0; padding: 0; box-sizing: border-box; }
  html, body {
    width: 1189px; height: 1200px; overflow: hidden;
    background: var(--backdrop);
    font-family: "Noto Sans", sans-serif;
    color: var(--ink);
  }
  .canvas { position: relative; width: 1189px; height: 1200px; }
  .card {
    position: absolute; left: 171px; width: 856px; height: 488px;
    background: var(--card); border-radius: 23px;
    box-shadow: 0 2px 6px rgba(0,0,0,0.12);
  }
  .card--front { top: 67px; display: flex; align-items: center; justify-content: center; }
  .card--back { top: 627px; }

  .brand { display: flex; align-items: center; gap: 14px; }
  .brand__mark { background: var(--ink); }
  .brand__name { font-weight: 700; color: var(--ink); line-height: 1; letter-spacing: 2px; }
  .brand--large .brand__mark { width: 44px; height: 44px; }
  .brand--large .brand__name { font-size: 104px; }
  .brand--small { position: absolute; left: 62px; top: 190px; gap: 11px; }
  .brand--small .brand__mark { width: 35px; height: 35px; }
  .brand--small .brand__name { font-size: 80px; }

  .divider { position: absolute; left: 419px; top: 89px; width: 2px; height: 311px; background: var(--rule); }

  .details { position: absolute; left: 455px; top: 100px; }
  .details__name { font-size: 32px; font-weight: 700; line-height: 1; letter-spacing: 0.3px; }
  .details__role { font-size: 23px; line-height: 1.2; margin-top: 2px; }
  .details__address { font-size: 23px; line-height: 30px; margin-top: 58px; }
  .contacts { list-style: none; margin-top: 12px; }
  .contacts__item { display: flex; align-items: center; gap: 10px; font-size: 23px; height: 31px; }
  .contacts__icon { width: 27px; height: 27px; flex: none; }
</style>
</head>
<body>
<main class="canvas">
  <section class="card card--front">
    <div class="brand brand--large">
      <span class="brand__mark"></span>
      <span class="brand__name">LUMA</span>
    </div>
  </section>

  <section class="card card--back">
    <div class="brand brand--small">
      <span class="brand__mark"></span>
      <span class="brand__name">LUMA</span>
    </div>
    <div class="divider"></div>
    <div class="details">
      <p class="details__name">EMPLOYEE NAME</p>
      <p class="details__role">Development Manager</p>
      <p class="details__address">P.O. Box 000,2nd Lane<br>Harbour Row, New Zealand</p>
      <ul class="contacts">
        <li class="contacts__item">
          <svg class="contacts__icon" viewBox="0 0 27 27" aria-hidden="true">
            <rect width="27" height="27" rx="4" fill="var(--ink)"/>
            <rect x="9" y="4" width="9" height="19" rx="1.5" fill="none" stroke="#fff" stroke-width="1.6"/>
            <rect x="11" y="7" width="5" height="5" fill="#fff"/>
            <g fill="#fff"><rect x="11" y="14" width="1.5" height="1.5"/><rect x="14.5" y="14" width="1.5" height="1.5"/><rect x="11" y="17" width="1.5" height="1.5"/><rect x="14.5" y="17" width="1.5" height="1.5"/></g>
          </svg>
          <span>(318) 4207265518</span>
        </li>
        <li class="contacts__item">
          <svg class="contacts__icon" viewBox="0 0 27 27" aria-hidden="true">
            <rect width="27" height="27" rx="4" fill="var(--ink)"/>
            <rect x="5" y="8" width="17" height="12" fill="none" stroke="#fff" stroke-width="1.6"/>
            <path d="M5 8 L13.5 15 L22 8" fill="none" stroke="#fff" stroke-width="1.6"/>
          </svg>
          <span>your@yourgmail.com</span>
        </li>
        <li class="contacts__item">
          <svg class="contacts__icon" viewBox="0 0 27 27" aria-hidden="true">
            <rect width="27" height="27" rx="4" fill="var(--ink)"/>
            <g fill="none" stroke="#fff" stroke-width="1.3">
              <circle cx="13.5" cy="13.5" r="8"/>
              <ellipse cx="13.5" cy="13.5" rx="3.5" ry="8"/>
              <line x1="5.5" y1="13.5" x2="21.5" y2="13.5"/>
              <line x1="7" y1="9.5" x2="20" y2="9.5"/>
              <line x1="7" y1="17.5" x2="20" y2="17.5"/>
            </g>
          </svg>
          <span>www.lumadrift.com</span>
        </li>
      </ul>
    </div>
  </section>
</main>
</body>
</html>
```